Professional Package for CPA Firm

We would like a stationery design for our new CPA Firm based in Atlanta, GA called 'Vale 8'. We work with investors to help grow investments, tax free. We would like the design to have a professional/minimal look with a 'wow' factor. We need 9.5″ x 4.125″, 9x12, and 10x13 mailing envelopes, business cards, and a letterhead. We have a logo that is already complete. For the letterhead, we would like to have space to put credentials at the bottom of the page

Industry/Entity Type

CPA, Accounting

```html
<!DOCTYPE html>
<html lang="en">
<head>
<meta charset="UTF-8">
<title>Vale 8 Business Card</title>
<link href="https://fonts.googleapis.com/css2?family=Lato:wght@400;700&family=Montserrat:wght@700&family=Dancing+Script:wght@500&display=swap" rel="stylesheet">
<style>
  :root {
    --backdrop: #8c8c8c;
    --card-white: #ffffff;
    --card-black: #050505;
    --ink-dark: #1f1f1f;
    --ink-mid: #6b6b6b;
    --accent-blue: #2aa6e0;
    --paper-light: #f4f4f4;
  }
  * { margin: 0; padding: 0; box-sizing: border-box; }
  html, body { width: 1200px; height: 800px; overflow: hidden; }
  body {
    background: var(--backdrop);
    font-family: "Lato", sans-serif;
    position: relative;
  }
  .card {
    position: absolute;
    top: 246px;
    width: 540px;
    height: 309px;
    border-bottom: 3px solid var(--accent-blue);
    box-shadow: 0 10px 28px rgba(0,0,0,0.28);
  }
  .card--front { left: 40px; background: var(--card-white); }
  .card--back { left: 620px; background: var(--card-black); }

  .identity {
    position: absolute;
    right: 292px;
    top: 108px;
    text-align: right;
    color: var(--ink-mid);
    font-size: 13px;
    line-height: 1.35;
  }
  .identity__name {
    color: var(--ink-dark);
    font-size: 19px;
    font-weight: 700;
    letter-spacing: 0.5px;
    margin-bottom: 2px;
  }
  .divider {
    position: absolute;
    left: 266px;
    top: 104px;
    width: 1px;
    height: 80px;
    background: var(--accent-blue);
  }
  .contact {
    position: absolute;
    left: 282px;
    top: 110px;
    list-style: none;
    color: var(--ink-mid);
    font-size: 13px;
    line-height: 1.35;
  }
  .contact li { display: flex; align-items: center; gap: 7px; }
  .contact svg { width: 10px; height: 10px; flex: none; }

  .brand {
    position: absolute;
    left: 0; right: 0;
    top: 92px;
    display: flex;
    justify-content: center;
    align-items: center;
    gap: 12px;
    color: var(--paper-light);
  }
  .brand__mark {
    width: 16px; height: 16px;
    background: var(--paper-light);
  }
  .brand__name {
    font-family: "Montserrat", sans-serif;
    font-weight: 700;
    font-size: 54px;
    letter-spacing: 1px;
  }
  .tagline {
    position: absolute;
    left: 0; right: 0;
    top: 210px;
    text-align: center;
    color: var(--paper-light);
    font-family: "Dancing Script", cursive;
    font-size: 30px;
  }
</style>
</head>
<body>
  <section class="card card--front">
    <div class="identity">
      <p class="identity__name">DANIEL HART</p>
      <p>President</p>
      <p>4120 Birchwood Lane</p>
      <p>Atlanta, Georgia 30301</p>
    </div>
    <span class="divider"></span>
    <ul class="contact">
      <li><svg viewBox="0 0 10 10"><path d="M2 1h2l1 2.5-1.2.8a5 5 0 0 0 2 2L6.6 5 9 6v2c0 .6-.5 1-1 1A8 8 0 0 1 1 2c0-.5.4-1 1-1z" fill="#1f1f1f"/></svg>555-214-7730</li>
      <li><svg viewBox="0 0 10 10"><rect x="1" y="1" width="8" height="8" fill="none" stroke="#1f1f1f" stroke-width="1.2"/></svg>555-318-6642</li>
      <li><svg viewBox="0 0 10 10"><rect x="0.5" y="1.5" width="9" height="7" fill="#1f1f1f"/><path d="M1 2l4 3.5L9 2" fill="none" stroke="#fff" stroke-width="1"/></svg>info@vale8.com</li>
      <li><svg viewBox="0 0 10 10"><circle cx="5" cy="5" r="4.5" fill="#1f1f1f"/><path d="M.5 5h9M5 .5c-2 2.5-2 6.5 0 9M5 .5c2 2.5 2 6.5 0 9" fill="none" stroke="#fff" stroke-width=".7"/></svg>www.vale8.com</li>
    </ul>
  </section>

  <section class="card card--back">
    <div class="brand">
      <span class="brand__mark"></span>
      <span class="brand__name">Vale 8</span>
    </div>
    <p class="tagline">Grow Your Investments Tax-Free</p>
  </section>
</body>
</html>
```